Specialised investor in e-mobility and energy wants business card design

We need a business card design that fits our existing corporate design. <The look and feel must be 'sharp'/'clean', dynamic, communicate momentum, professionalism etc (as one would imagine from a firm in the financial sector). We like the idea of a reverse-side of the card that includes the logo, and the name and contact details on the other. We expect the deliverable to be whatever format might be required to be able to get cards printed directly by a service such as kelmo press. Our website is www.zub.capital

```html
<!DOCTYPE html>
<html lang="en">
<head>
<meta charset="utf-8">
<title>Zub Capital – Business Card</title>
<link href="https://fonts.googleapis.com/css2?family=Arimo:wght@400;700&display=swap" rel="stylesheet">
<style>
  :root {
    --backdrop: #1b1c1b;
    --paper: #f6f6f2;
    --forest: #27401b;
    --leaf: #72a83c;
    --leaf-soft: #7aa545;
    --ink: #4a4a4a;
    --rule: #6b6b6b;
  }
  * { margin: 0; padding: 0; box-sizing: border-box; }
  html, body {
    width: 1200px; height: 963px; overflow: hidden;
    background: var(--backdrop);
    font-family: "Arimo", Arial, sans-serif;
  }
  .sheet {
    position: relative; width: 1200px; height: 963px;
    display: flex; flex-direction: column; align-items: center; justify-content: center; gap: 60px;
  }
  .card {
    position: relative; width: 700px; height: 400px;
    border-radius: 26px; overflow: hidden;
    box-shadow: 0 14px 30px rgba(0,0,0,.55);
  }
  /* front */
  .card--front {
    background: var(--paper);
    border-bottom: 5px solid var(--leaf);
  }
  .brand {
    position: absolute; display: flex; align-items: center; gap: 12px;
    font-weight: 400; letter-spacing: 1px; white-space: nowrap;
  }
  .brand__dot { width: 18px; height: 18px; border-radius: 50%; background: var(--leaf); }
  .card--front .brand { left: 62px; top: 160px; font-size: 44px; color: var(--forest); }
  .divider {
    position: absolute; left: 368px; top: 110px; width: 1.5px; height: 190px; background: var(--rule);
  }
  .contact { position: absolute; left: 400px; top: 118px; color: var(--ink); }
  .contact__name { font-weight: 700; font-size: 22px; letter-spacing: 1px; color: var(--forest); }
  .contact__name .surname { color: var(--leaf); }
  .contact__place { font-size: 18px; margin: 12px 0 20px; }
  .contact__list { list-style: none; font-size: 18px; }
  .contact__list li { display: flex; align-items: center; gap: 10px; margin-bottom: 9px; }
  .contact__list svg { width: 17px; height: 17px; fill: var(--leaf); flex: none; }
  /* back */
  .card--back { background: var(--forest); }
  .card--back .arc { position: absolute; inset: 0; width: 100%; height: 100%; }
  .card--back .brand { right: 60px; top: 110px; font-size: 54px; color: var(--paper); }
  .card--back .brand__dot { width: 20px; height: 20px; background: var(--paper); }
</style>
</head>
<body>
<main class="sheet">
  <section class="card card--front" aria-label="Card front">
    <div class="brand"><span class="brand__dot"></span>Zub Capital</div>
    <div class="divider"></div>
    <div class="contact">
      <p class="contact__name">MARTEN <span class="surname">ELLWOOD</span></p>
      <p class="contact__place">Geneva, Switzerland</p>
      <ul class="contact__list">
        <li><svg viewBox="0 0 24 24"><path d="M6.6 10.8a15 15 0 0 0 6.6 6.6l2.2-2.2c.3-.3.7-.4 1-.2 1.1.4 2.3.6 3.6.6.6 0 1 .4 1 1V20c0 .6-.4 1-1 1A17 17 0 0 1 3 4c0-.6.4-1 1-1h3.5c.6 0 1 .4 1 1 0 1.3.2 2.5.6 3.6.1.3 0 .7-.2 1z"/></svg>+41 79555 0142</li>
        <li><svg viewBox="0 0 24 24"><path d="M2 5h20v14H2z M2 5l10 8 10-8" fill="none" stroke="#72a83c" stroke-width="2"/></svg>marten@zub.capital</li>
        <li><svg viewBox="0 0 24 24"><circle cx="12" cy="12" r="9" fill="none" stroke="#72a83c" stroke-width="2"/><path d="M3 12h18M12 3c3 3 3 15 0 18M12 3c-3 3-3 15 0 18" fill="none" stroke="#72a83c" stroke-width="1.6"/></svg>www.zub.capital</li>
      </ul>
    </div>
  </section>

  <section class="card card--back" aria-label="Card back">
    <svg class="arc" viewBox="0 0 700 400" preserveAspectRatio="none" aria-hidden="true">
      <ellipse cx="-40" cy="470" rx="410" ry="420" fill="var(--leaf)" stroke="var(--paper)" stroke-width="16"/>
    </svg>
    <div class="brand"><span class="brand__dot"></span>Zub Capital</div>
  </section>
</main>
</body>
</html>
```